New Mechanical Maintenance business needs website

New Mechanical Maintenance business in Perth Western Australia needs a nice and easy to navigate website. Showing what we do and how we can be the right fit for other small to medium size business by offering personalized service from our highly skilled team. We deal with both fixed plant repairs like food and chemical processing facilities to heavy equipment like drill rigs, Large boats and earthmoving equipment.

Target Market(s)

Small to medium business to offer personalized services/packages

Industry/Entity Type

e deal with both fixed plant repairs like food and chemical processing facilities to heavy equipment like drill rigs, Large boats and earthmoving equipment.

Coding

Coded - Design and coding required

Number of Pages Required

4 page

Font styles to use
Serif

Colors
0054AA
0677BA
7BADD7
CADEEF
E8F1F8

Requirements
Must have
• A website that is easy to navigate but covers off on the range of services/maintenance we can provide

```html
<!DOCTYPE html>
<html lang="en">
<head>
<meta charset="utf-8">
<title>Keelrock Maintenance</title>
<link href="https://fonts.googleapis.com/css2?family=Days+One&family=Lato:wght@400;700&display=swap" rel="stylesheet">
<style>
:root{
  --blue:#0054AA;--blue2:#0677BA;--sky:#7BADD7;--pale:#CADEEF;--mist:#E8F1F8;
  --ink:#1d1d1d;--text:#555;--white:#fff;--black:#0b0b0b;
}
*{margin:0;padding:0;box-sizing:border-box}
html,body{width:1200px;height:4062px;overflow:hidden}
body{position:relative;font-family:"Lato",sans-serif;color:var(--text);background:var(--white)}
.abs{position:absolute}
.display{font-family:"Days One",sans-serif;color:var(--ink);letter-spacing:.5px;white-space:nowrap}
.btn{position:absolute;display:flex;align-items:center;justify-content:center;border-radius:24px;color:var(--white);font-weight:700;background:var(--blue);font-size:17px}
.btn.light{background:var(--blue2);font-size:21px}
.topbar{left:0;top:0;width:1200px;height:49px;background:var(--blue);color:var(--white);font-size:16px;display:flex;align-items:center;justify-content:center}
.topbar b{margin:0 4px}
.brand{display:flex;align-items:center;gap:10px}
.brand .dot{width:44px;height:44px;border-radius:50%;background:var(--blue)}
.brand span{font-weight:700;font-size:26px;color:var(--ink);line-height:1}
.nav{top:133px;font-size:18px;color:#444}
.hero{left:0;top:177px;width:1200px;height:589px;background:linear-gradient(90deg,#4a4744 0%,#2b2e33 40%,#141518 70%,#0c0c0e 100%)}
.hero h1{position:absolute;right:112px;text-align:right;font-family:"Days One",sans-serif;color:var(--white);font-size:52px;font-weight:400;letter-spacing:1.5px;line-height:88px;top:104px;white-space:nowrap}
.hero p{position:absolute;right:112px;top:284px;width:600px;text-align:right;color:#eee;font-size:22px;line-height:36px}
.h2{font-size:30px;font-weight:400}
.rule{height:3px;width:126px;background:var(--blue)}
.body{font-size:16px;line-height:32px}
.photo{position:absolute}
.services{left:0;top:1438px;width:1200px;height:1199px;background:var(--mist)}
.card h3{font-family:"Days One",sans-serif;font-weight:400;font-size:18px;color:var(--ink);letter-spacing:.5px;position:absolute;white-space:nowrap}
.card p{position:absolute;font-size:14px;line-height:27px;width:305px;color:#666}
.testi{left:0;top:2637px;width:1200px;height:451px;background:radial-gradient(ellipse at 50% 30%,#1f6cd0 0%,#0a48a8 45%,#073a95 100%)}
.testi p{position:absolute;left:140px;width:920px;top:108px;text-align:center;color:var(--white);font-size:17px;line-height:36px}
.why .box{position:absolute;top:3320px;width:292px;height:326px;background:var(--white);box-shadow:0 4px 18px rgba(0,0,0,.09)}
.box .ic{position:absolute;left:102px;top:31px;width:88px;height:88px;border-radius:50%;border:6px solid var(--blue);display:flex;align-items:center;justify-content:center}
.box h4{position:absolute;top:142px;width:100%;text-align:center;font-size:14px;color:var(--ink);font-weight:700;letter-spacing:.5px}
.box p{position:absolute;top:167px;left:20px;width:252px;text-align:center;font-size:13px;line-height:26.5px;color:#777}
footer{position:absolute;left:0;top:3731px;width:1200px;height:331px;background:var(--black);color:var(--white)}
footer .fnav{position:absolute;top:181px;font-size:18px}
.soc{position:absolute;top:236px;width:34px;height:34px;border-radius:50%;background:var(--blue)}
</style>
</head>
<body>

<div class="abs topbar">Call us today on <b>+61 8 5550 1234</b> for a free onsite quotation or email <b>info@keelrockmaint.com.au</b></div>

<header>
  <div class="abs brand" style="left:113px;top:91px"><div class="dot"></div><span>KEELROCK</span></div>
  <div class="btn light" style="left:711px;top:73px;width:218px;height:45px">+61 8 5550 1234</div>
  <div class="btn" style="left:944px;top:73px;width:143px;height:45px">Contact Us</div>
  <div class="abs nav" style="left:295px">Home</div>
  <div class="abs nav" style="left:408px">About Us</div>
  <div class="abs nav" style="left:549px">What We Do</div>
  <div class="abs nav" style="left:716px">Where We Come From</div>
  <div class="abs nav" style="left:963px">Why Choose Us</div>
</header>

<section class="abs hero">
  <div class="abs" role="img" aria-label="Engineer in hard hat and safety glasses inspecting machinery" style="left:0;top:0;width:640px;height:589px;background:linear-gradient(90deg,rgba(120,90,80,.35),rgba(0,0,0,0))"></div>
  <h1>WELCOME TO<br>KEELROCK MAINTENANCE</h1>
  <p>At vero eos et accusamus et iusto odio dignissimos ducimus qui blanditiis praesentium voluptatum deleniti atque corrupti quos dolores et quas molestias</p>
  <div class="btn light" style="left:711px;top:421px;width:216px;height:44px">+61 8 5550 1234</div>
  <div class="btn" style="left:943px;top:421px;width:142px;height:44px;background:var(--blue2)">Get A Quote</div>
</section>

<section class="origin">
  <h2 class="abs display h2" style="left:113px;top:878px">WHERE WE COME FROM</h2>
  <div class="abs rule" style="left:113px;top:934px"></div>
  <p class="abs body" style="left:113px;top:959px;width:470px">Director of the company has over 20-year experience in the fixed and mobile plant industries ranging from Perth local and overseas. Facilities like precious metals refining, offshore drilling and production platform, open cut and underground mining, civils, geotechnical and construction equipment and large-scale construction as an expat overseas.</p>
  <p class="abs body" style="left:113px;top:1184px;width:470px">We offer personalised service to all small and medium size business across a diverse range of industries.</p>
  <div class="btn" style="left:113px;top:1277px;width:135px;height:45px">Read More</div>
  <div class="photo" role="img" aria-label="Mechanics working on industrial equipment in a workshop" style="left:601px;top:880px;width:487px;height:446px;background:linear-gradient(160deg,#5a6b7a,#2a3540 60%,#1a2026)"></div>
</section>

<section class="abs services">
  <h2 class="abs display h2" style="left:112px;top:92px">WHAT WE DO</h2>
  <div class="abs rule" style="left:112px;top:149px"></div>
</section>

<div class="card">
  <div class="photo" role="img" aria-label="Oil pump jacks at sunset" style="left:112px;top:1634px;width:309px;height:222px;background:linear-gradient(180deg,#8a7fb0,#e0a27a 60%,#2a2020)"></div>
  <div class="photo" role="img" aria-label="Large ship in dry dock" style="left:446px;top:1634px;width:308px;height:222px;background:linear-gradient(180deg,#bcd0e0,#9a8d80 55%,#6d4a36)"></div>
  <div class="photo" role="img" aria-label="Orange excavator on a work site" style="left:779px;top:1634px;width:309px;height:222px;background:linear-gradient(135deg,#4f7a44,#c76a35 55%,#7d7b76)"></div>
  <h3 style="left:112px;top:1884px">DRILL RIGS</h3>
  <h3 style="left:446px;top:1884px">LARGE BOATS</h3>
  <h3 style="left:779px;top:1884px">EARTHMOVING EQUIPMENT</h3>
  <p style="left:112px;top:1918px">At vero eos et accusamus et iusto odio dignissimos ducimus qui blanditiis praesentium voluptatum deleniti atque corrupti quos dolores et quas molestias excepturi sint</p>
  <p style="left:446px;top:1918px">At vero eos et accusamus et iusto odio dignissimos ducimus qui blanditiis praesentium voluptatum deleniti atque corrupti quos dolores et quas molestias excepturi sint</p>
  <p style="left:779px;top:1918px">At vero eos et accusamus et iusto odio dignissimos ducimus qui blanditiis praesentium voluptatum deleniti atque corrupti quos dolores et quas molestias excepturi sint</p>

  <div class="photo" role="img" aria-label="Milling machine cutting metal" style="left:112px;top:2066px;width:309px;height:222px;background:linear-gradient(135deg,#9aa3aa,#55606a 60%,#2e3338)"></div>
  <div class="photo" role="img" aria-label="Drafting plans with tools and a hard hat" style="left:446px;top:2066px;width:308px;height:222px;background:linear-gradient(135deg,#c9a46a,#e3d9c6 50%,#a88a5a)"></div>
  <div class="photo" role="img" aria-label="Team reviewing work in a fabrication plant" style="left:779px;top:2066px;width:309px;height:222px;background:linear-gradient(180deg,#d8dde0,#8f9a96 55%,#3d4a3a)"></div>
  <h3 style="left:112px;top:2317px">MILLING MACHINING</h3>
  <h3 style="left:446px;top:2317px">DESIGN &amp; DRAFTING</h3>
  <h3 style="left:779px;top:2317px">FIXED PLANT REPAIRS</h3>
  <p style="left:112px;top:2350px">At vero eos et accusamus et iusto odio dignissimos ducimus qui blanditiis praesentium voluptatum deleniti atque corrupti quos dolores et quas molestias excepturi sint</p>
  <p style="left:446px;top:2350px">At vero eos et accusamus et iusto odio dignissimos ducimus qui blanditiis praesentium voluptatum deleniti atque corrupti quos dolores et quas molestias excepturi sint</p>
  <p style="left:779px;top:2350px">At vero eos et accusamus et iusto odio dignissimos ducimus qui blanditiis praesentium voluptatum deleniti atque corrupti quos dolores et quas molestias excepturi sint</p>
  <div class="btn" style="left:112px;top:2496px;width:285px;height:45px">Contact Us For A Free Quote</div>
</div>

<section class="abs testi" role="img" aria-label="Blue background with welding sparks">
  <p>" I must explain to you how all this mistaken idea of denouncing pleasure and praising pain was born and I will give you a complete account of the system, and expound the actual teachings of the great explorer of the truth, the master-builder of human happiness. No one rejects, dislikes, or avoids pleasure itself, because it is pleasure, but because those who do not know how to pursue pleasure rationally encounter consequences that are extremely painful "</p>
  <div class="abs" style="left:0;width:1200px;top:278px;text-align:center;color:var(--white);font-size:18px;letter-spacing:2px">★★★★☆</div>
  <div class="abs display" style="left:0;width:1200px;top:313px;text-align:center;color:var(--white);font-size:18px">- DANIEL HARTLEY</div>
  <svg class="abs" style="left:1128px;top:178px" width="12" height="92">
    <circle cx="6" cy="6" r="5.5" fill="#fff"/><circle cx="6" cy="26" r="5.5" fill="#fff"/><circle cx="6" cy="46" r="5.5" fill="#2a8ae0"/><circle cx="6" cy="66" r="5.5" fill="#fff"/><circle cx="6" cy="86" r="5.5" fill="#fff"/>
  </svg>
</section>

<section class="why">
  <h2 class="abs display h2" style="left:0;width:1200px;text-align:center;top:3168px">WHY CHOOSE US</h2>
  <div class="abs rule" style="left:537px;top:3226px"></div>
  <p class="abs" style="left:0;width:1200px;text-align:center;top:3258px;font-size:17px;color:#666">I must explain to you how all this mistaken idea of was born and I will give you a complete</p>

  <div class="box" style="left:132px">
    <div class="ic"><svg width="40" height="40" viewBox="0 0 40 40" fill="none" stroke="#0054AA" stroke-width="2.5" stroke-linecap="round"><path d="M8 32 L30 10"/><path d="M32 32 L10 10"/><circle cx="8" cy="9" r="4"/><circle cx="32" cy="9" r="4"/></svg></div>
    <h4>DIGNISSIMOS DUCIMUS BLAND</h4>
    <p>I must explain to you how all this mistaken idea of denouncing pleasure and praising pain was born and I will give you a complete account of the system, and expound the actual</p>
  </div>
  <div class="box" style="left:454px">
    <div class="ic"><svg width="40" height="40" viewBox="0 0 40 40" fill="none" stroke="#0054AA" stroke-width="2.5" stroke-linecap="round"><circle cx="20" cy="15" r="7"/><path d="M8 34 C8 26 32 26 32 34"/><path d="M11 12 H29"/></svg></div>
    <h4>DIGNISSIMOS DUCIMUS BLAND</h4>
    <p>I must explain to you how all this mistaken idea of denouncing pleasure and praising pain was born and I will give you a complete account of the system, and expound the actual</p>
  </div>
  <div class="box" style="left:777px">
    <div class="ic"><svg width="40" height="40" viewBox="0 0 40 40" fill="none" stroke="#0054AA" stroke-width="2.5" stroke-linecap="round"><circle cx="18" cy="18" r="8"/><circle cx="18" cy="18" r="3"/><path d="M18 5v4M18 27v4M5 18h4M27 18h4"/><path d="M22 34 H36 V30 C36 26 22 26 22 30 Z"/></svg></div>
    <h4>DIGNISSIMOS DUCIMUS BLAND</h4>
    <p>I must explain to you how all this mistaken idea of denouncing pleasure and praising pain was born and I will give you a complete account of the system, and expound the actual</p>
  </div>
</section>

<footer>
  <div class="abs brand" style="left:510px;top:71px"><div class="dot" style="background:var(--white)"></div><span style="color:var(--white)">KEELROCK</span></div>
  <div class="fnav" style="left:204px">Home</div>
  <div class="fnav" style="left:317px">About Us</div>
  <div class="fnav" style="left:457px">What We Do</div>
  <div class="fnav" style="left:624px">Where We Come From</div>
  <div class="fnav" style="left:871px">Why Choose Us</div>
  <div class="soc" style="left:485px"></div>
  <div class="soc" style="left:534px"></div>
  <div class="soc" style="left:583px"></div>
  <div class="soc" style="left:632px"></div>
  <div class="soc" style="left:681px"></div>
  <div class="abs" style="left:0;width:1200px;text-align:center;top:291px;font-size:15px">(C) Copyright 2024 | All Rights Reserved</div>
</footer>

</body>
</html>
```